Yard sign

Looking for a yard sign. <br/>Something simple, name, number. <br/>Large text, readable from 50 feet away. <br/><br/>18 x 24 inches.

Target Market(s)

Potential homeowners thinking about going solar.

Colors

Designer to choose colors to be used in the design.

Requirements
Must have
• "WE'VE GONE SOLAR!"
Nice to have
• We are a solar company, we would like a design that compliments the homeowners decision that they went solar and encourages others to do the same.

```html
<!DOCTYPE html>
<html lang="en">
<head>
<meta charset="utf-8">
<title>Brightfield Solar Yard Sign</title>
<link rel="stylesheet" href="https://fonts.googleapis.com/css2?family=Roboto+Condensed:wght@700&family=Roboto:wght@900&display=swap">
<style>
  :root {
    --page-bg: #1b1819;
    --board-center: #4a4949;
    --board-edge: #1f1f1f;
    --sun-yellow: #fcc92b;
    --brand-orange: #f78f1e;
    --band-red: #dc4308;
    --ink-black: #0b0b0b;
    --white: #ffffff;
  }
  html, body {
    margin: 0;
    padding: 0;
    width: 1200px;
    height: 1200px;
    overflow: hidden;
    background: var(--page-bg);
  }
  .yard-sign {
    position: absolute;
    left: 76px;
    top: 207px;
    width: 1048px;
    height: 786px;
  }
  .yard-sign svg { display: block; }
  .brand-name {
    font-family: "Roboto Condensed", "Arial Narrow", sans-serif;
    font-weight: 700;
    fill: var(--brand-orange);
  }
  .tagline {
    font-family: "Roboto Condensed", "Arial Narrow", sans-serif;
    font-weight: 700;
    font-size: 38px;
    letter-spacing: 3px;
    fill: var(--white);
  }
  .rep-name {
    font-family: "Roboto Condensed", "Arial Narrow", sans-serif;
    font-weight: 700;
    font-size: 64px;
    letter-spacing: -1.5px;
    fill: var(--sun-yellow);
  }
  .phone-number {
    font-family: "Roboto Condensed", "Arial Narrow", sans-serif;
    font-weight: 700;
    font-size: 112px;
    fill: var(--sun-yellow);
  }
  .web-address {
    font-family: "Roboto", Arial, sans-serif;
    font-weight: 900;
    font-size: 50px;
    fill: var(--ink-black);
  }
</style>
</head>
<body>
  <div class="yard-sign">
    <svg width="1048" height="786" viewBox="0 0 1048 786" xmlns="http://www.w3.org/2000/svg">
      <defs>
        <radialGradient id="board-glow" cx="0.5" cy="0.6" r="0.65">
          <stop offset="0" stop-color="#4a4949"/>
          <stop offset="1" stop-color="#1f1f1f"/>
        </radialGradient>
      </defs>

      <rect class="board" width="1048" height="786" fill="url(#board-glow)"/>

      <!-- brand block -->
      <circle class="brand-mark" cx="300" cy="225" r="76" fill="var(--sun-yellow)"/>
      <text class="brand-name" x="398" y="252" font-size="84">BRIGHTFIELD</text>
      <text class="brand-name" x="400" y="300" font-size="44" letter-spacing="10">SOLAR</text>

      <!-- headline -->
      <text class="tagline" x="524" y="392" text-anchor="middle">WE'VE GONE SOLAR!</text>

      <!-- representative -->
      <text class="rep-name" x="524" y="489" text-anchor="middle">DANIEL MARSH</text>

      <!-- lower bands -->
      <polygon class="accent-wedge" points="564,545 1048,475 1048,612" fill="var(--sun-yellow)"/>
      <polygon class="contact-band" points="0,472 1048,626 1048,786 0,786" fill="var(--band-red)"/>

      <!-- phone -->
      <g class="phone-icon" transform="translate(203 656)">
        <circle r="40" fill="none" stroke="var(--sun-yellow)" stroke-width="4"/>
        <circle r="34" fill="var(--band-red)"/>
        <path d="M-16,-16 q-6,4 -2,16 q8,16 22,22 q10,3 14,-3 l-8,-8 q-4,3 -8,0 q-8,-6 -12,-12 q-2,-4 2,-7 z" fill="var(--white)"/>
        <path d="M2,-14 a14,14 0 0 1 12,12 M2,-22 a22,22 0 0 1 20,20" fill="none" stroke="var(--white)" stroke-width="2.5" stroke-linecap="round"/>
      </g>
      <text class="phone-number" x="259" y="690">555-014-2290</text>

      <!-- web -->
      <text class="web-address" x="524" y="753" text-anchor="middle">www.bfsolar.net</text>
    </svg>
  </div>
</body>
</html>
```